Vantiqo custom business card design

Need a authentic, innovative business card design for a new mobile app business. I am uploading a few screen images from our app for you to view. I would like app design theme to match business card design. I can also send logo images.

```html
<!DOCTYPE html>
<html lang="en">
<head>
<meta charset="utf-8">
<title>Vantiqo Business Card</title>
<link rel="stylesheet" href="https://fonts.googleapis.com/css2?family=Source+Sans+3:wght@400;700;900&display=swap">
<style>
  :root {
    --page-bg: #e9e6e2;
    --purple-light: #5b2d8c;
    --purple-mid: #4a1f78;
    --purple-deep: #2a0a58;
    --card-dark: #141414;
    --frost: rgba(226, 226, 232, 0.9);
    --frost-edge: rgba(255, 255, 255, 0.95);
    --text-light: #f1ecf6;
    --text-soft: #ddd3e8;
    --brand-ink: #0d0d0d;
  }
  * { margin: 0; padding: 0; box-sizing: border-box; }
  html, body {
    width: 1200px;
    height: 1120px;
    overflow: hidden;
    background: var(--page-bg);
    font-family: "Source Sans 3", sans-serif;
  }
  .business-card {
    position: absolute;
    left: 100px;
    top: 275px;
    width: 1000px;
    height: 570px;
    overflow: hidden;
    background: linear-gradient(90deg,
      var(--purple-mid) 0%,
      var(--purple-light) 22%,
      var(--purple-deep) 46%,
      #1b1420 66%,
      var(--card-dark) 100%);
    box-shadow: 0 18px 40px rgba(0, 0, 0, 0.25);
  }
  .clear-window {
    position: absolute;
    left: 365px;
    top: 0;
    width: 570px;
    height: 570px;
  }
  .identity {
    position: absolute;
    left: 46px;
    top: 48px;
    color: var(--text-light);
  }
  .identity .person-name {
    font-size: 34px;
    font-weight: 700;
    letter-spacing: 0.5px;
    line-height: 1.1;
  }
  .identity .person-role {
    font-size: 24px;
    font-weight: 400;
    line-height: 1.2;
    margin-top: 2px;
  }
  .address {
    position: absolute;
    left: 46px;
    top: 274px;
    font-size: 24px;
    line-height: 32px;
    color: var(--text-soft);
    font-style: normal;
  }
  .contact-list {
    position: absolute;
    left: 46px;
    top: 352px;
    list-style: none;
    color: var(--text-soft);
    font-size: 24px;
    line-height: 33px;
  }
  .contact-list li {
    display: flex;
    align-items: center;
  }
  .contact-list .icon {
    width: 22px;
    height: 22px;
    margin-right: 21px;
    fill: var(--text-soft);
    flex: none;
  }
  .brand-name {
    position: absolute;
    left: 650px;
    top: 372px;
    transform: translateX(-50%);
    font-size: 54px;
    font-weight: 900;
    color: var(--brand-ink);
    letter-spacing: 0.5px;
    line-height: 1;
  }
</style>
</head>
<body>
  <div class="business-card">
    <svg class="clear-window" viewBox="0 0 570 570" aria-hidden="true">
      <defs>
        <radialGradient id="frostFill" cx="45%" cy="40%" r="65%">
          <stop offset="0%" stop-color="#ecebef" stop-opacity="0.95"/>
          <stop offset="70%" stop-color="#d9d7de" stop-opacity="0.9"/>
          <stop offset="100%" stop-color="#c4c1cb" stop-opacity="0.88"/>
        </radialGradient>
      </defs>
      <circle cx="285" cy="285" r="280" fill="url(#frostFill)" stroke="var(--frost-edge)" stroke-width="2"/>
    </svg>

    <div class="identity">
      <div class="person-name">MARLON FEYT</div>
      <div class="person-role">PRESIDENT</div>
    </div>

    <address class="address">
      2417 Harrowgate Lane<br>
      Cedar Bend, NY 11920
    </address>

    <ul class="contact-list">
      <li>
        <svg class="icon" viewBox="0 0 24 24" aria-label="Phone"><path d="M3 8c0-3 4-5 9-5s9 2 9 5v2h-5V8H8v2H3z M6 11h12l2 9H4z M12 13a3 3 0 1 0 0 6a3 3 0 1 0 0-6z"/></svg>
        <span>412 6038 1947</span>
      </li>
      <li>
        <svg class="icon" viewBox="0 0 24 24" aria-label="Mobile"><path d="M7 1h10a2 2 0 0 1 2 2v18a2 2 0 0 1-2 2H7a2 2 0 0 1-2-2V3a2 2 0 0 1 2-2zm0 3v14h10V4zm5 15.5a1.2 1.2 0 1 0 0 2.4a1.2 1.2 0 1 0 0-2.4z"/></svg>
        <span>739 2815 4062</span>
      </li>
      <li>
        <svg class="icon" viewBox="0 0 24 24" aria-label="Fax"><path d="M6 2h12v6H6z M2 9h20v9h-3v-3H5v3H2z M6 16h12v6H6z"/></svg>
        <span>615 9274 3081</span>
      </li>
      <li>
        <svg class="icon" viewBox="0 0 24 24" aria-label="Email"><path d="M2 5h20v2l-10 6L2 7z M2 9l10 6 10-6v10H2z"/></svg>
        <span>marlon@vantiqo.com</span>
      </li>
      <li>
        <svg class="icon" viewBox="0 0 24 24" aria-label="Website"><path d="M12 2a10 10 0 1 0 0 20a10 10 0 1 0 0-20zm-3 4c2 0 3 1 2 3s-3 1-3 3 2 2 2 4-1 3-2 3a8 8 0 0 1-3-13c1 0 2-1 4 0zm6 1c2 1 4 3 4 6c-1 0-2-1-3 0s0 3-1 4-2 0-2-2 2-2 1-4-1-2 1-4z"/></svg>
        <span>www.vantiqo.com</span>
      </li>
    </ul>

    <div class="brand-name">Vantiqo</div>
  </div>
</body>
</html>
```